Book cover for book about Climate Change

Looking for a clean, bold, and attractive cover for a mass-market paperback (5.5"x 8.5") about solving the climate change problem. Title is either "Where the Rivers Meet” or A Harbor Made of Glass” (your choice), subtitle is "A practical field guide to mending the weather — so that the young ones after us inherit steady seasons and open skies," author is Lorne Whitcombe. Thinking that it *might* feature an image of Earth (or a portion thereof) and its very thin layer of atmosphere -- but STRONGLY encourage other ideas too!

Requirements
Nice to have
• Keep it positive — NOT scary doom-and-gloom

```html
<!DOCTYPE html>
<html lang="en">
<head>
<meta charset="utf-8">
<title>Where the Rivers Meet — Lorne Whitcombe</title>
<link rel="stylesheet" href="https://fonts.googleapis.com/css2?family=Barlow:wght@700;800&family=Inter:wght@600&display=swap">
<style>
  :root {
    --page: #ffffff;
    --night-deep: #2e0f35;
    --night-mid: #3d1646;
    --night-glow: #4e2160;
    --gold: #f3b71b;
    --paper-white: #f8f9fc;
  }
  * { margin: 0; padding: 0; box-sizing: border-box; }
  html, body {
    width: 1200px;
    height: 1200px;
    overflow: hidden;
    background: var(--page);
  }
  .cover {
    position: absolute;
    left: 262px;
    top: 58px;
    width: 706px;
    height: 1090px;
    overflow: hidden;
  }
  .cover__sky {
    position: absolute;
    inset: 0;
    background:
      radial-gradient(ellipse 60% 45% at 52% 42%, var(--night-glow) 0%, rgba(78, 33, 96, 0) 100%),
      linear-gradient(180deg, var(--night-mid) 0%, var(--night-deep) 100%);
  }
  .cover__author {
    position: absolute;
    top: 80px;
    left: 0;
    right: 0;
    text-align: center;
    font-family: "Barlow", sans-serif;
    font-weight: 700;
    font-size: 48px;
    line-height: 1;
    letter-spacing: 0.16em;
    padding-left: 0.16em;
    color: var(--gold);
  }
  .cover__title {
    position: absolute;
    top: 205px;
    left: 0;
    right: 0;
    text-align: center;
    font-family: "Inter", sans-serif;
    font-weight: 600;
    font-size: 150px;
    line-height: 134px;
    letter-spacing: -0.055em;
    color: var(--paper-white);
  }
  .cover__title-line { display: block; }
  .cover__title-line--accent { color: var(--gold); }
  .cover__subtitle {
    position: absolute;
    top: 868px;
    left: 60px;
    right: 60px;
    text-align: center;
    font-family: "Barlow", sans-serif;
    font-weight: 700;
    font-size: 27px;
    line-height: 39px;
    text-transform: uppercase;
    color: var(--paper-white);
  }
  .cover__subtitle em {
    font-style: normal;
    color: var(--gold);
  }
</style>
</head>
<body>
  <main class="cover">
    <div class="cover__sky" role="img" aria-label="Deep violet night sky scattered with small white stars"></div>
    <p class="cover__author">LORNE WHITCOMBE</p>
    <h1 class="cover__title">
      <span class="cover__title-line">WHERE</span>
      <span class="cover__title-line">THE</span>
      <span class="cover__title-line">RIVERS</span>
      <span class="cover__title-line cover__title-line--accent">MEET</span>
    </h1>
    <p class="cover__subtitle">A <em>practical</em> field guide to <em>mending</em> the weather — so that the young ones after us inherit steady seasons and open skies.</p>
  </main>
</body>
</html>
```